I would like a business card to match my truck wrap and logo. I would like the font to match my existing business card please.

Industry/Entity Type

Painter

Contact Information for Business Card

Rodrigo Fenwar 801-437-2190 Fenwarcoatings.utah@brelmox.com
SERVICES - Custom Paint & Stain, Interior & Exterior, Epoxy Coatings / Garage Floors, Cabinet Refinishing, Log Staining and Refinishing.

Requirements
Nice to have
• I would like to have the white and grey line like the bottom of my vehicle wrap, Light Grey to match my truck also.

```html
<!DOCTYPE html>
<html lang="en">
<head>
<meta charset="utf-8">
<title>Fenwar Coatings – Business Card</title>
<link rel="stylesheet" href="https://fonts.googleapis.com/css2?family=Russo+One&family=Arimo:wght@400;700&display=swap">
<style>
  :root {
    --stage: #2b2b2d;
    --brand-blue: #1a86d6;
    --sky-blue: #03a9e9;
    --deep-blue: #0a5a9e;
    --paper-top: #e4e5e7;
    --paper-bottom: #ffffff;
    --band-grey: #b1b6c2;
    --band-line: #ffffff;
    --ink: #1d1d1f;
    --white: #ffffff;
  }
  * { margin: 0; padding: 0; box-sizing: border-box; }
  html, body {
    width: 1200px; height: 866px; overflow: hidden;
    background: var(--stage);
  }
  .sheet { position: relative; width: 1200px; height: 866px; }
  .card {
    position: absolute; left: 290px;
    width: 620px; height: 354px;
    overflow: hidden;
    box-shadow: 0 10px 24px rgba(0,0,0,.45);
  }
  .card--front { top: 49px; background: linear-gradient(160deg, var(--paper-top) 0%, var(--paper-bottom) 70%); }
  .card--back { top: 463px; background: linear-gradient(170deg, var(--sky-blue) 0%, #0a84cf 45%, var(--deep-blue) 100%); }
  .card__band { position: absolute; left: 0; top: 0; width: 620px; height: 354px; }

  .owner {
    position: absolute; left: 46px; top: 52px;
    font-family: "Russo One", sans-serif; font-size: 28px; font-weight: 400;
    color: var(--brand-blue); letter-spacing: 1px; text-transform: uppercase;
    line-height: 1;
  }
  .contact { position: absolute; left: 46px; top: 100px; list-style: none;
    font-family: "Arimo", Arial, sans-serif; font-size: 17px; color: var(--ink); }
  .contact li { display: flex; align-items: center; gap: 10px; margin-bottom: 8px; line-height: 1.1; }
  .contact svg { width: 18px; height: 18px; flex: none; }

  .brand { position: absolute; font-family: "Russo One", sans-serif; text-transform: uppercase; line-height: 1; }
  .brand--front { right: 40px; top: 182px; color: var(--brand-blue); display: flex; align-items: flex-start; gap: 14px; }
  .brand--back { left: 44px; top: 110px; color: var(--white); display: flex; align-items: flex-start; gap: 14px; }
  .brand__mark { width: 24px; height: 24px; background: currentColor; margin-top: 6px; }
  .brand__name { display: block; }
  .brand--front .brand__name { font-size: 48px; }
  .brand--back .brand__name { font-size: 40px; }
  .brand__sub { display: block; margin-top: 8px; }
  .brand--front .brand__sub { font-size: 17px; letter-spacing: 11px; }
  .brand--back .brand__sub { font-size: 14px; letter-spacing: 9px; }

  .services { position: absolute; left: 318px; top: 86px; color: var(--white);
    font-family: "Arimo", Arial, sans-serif; }
  .services__title { font-family: "Arimo", Arial, sans-serif; font-weight: 700; font-size: 18px; letter-spacing: .5px; margin-bottom: 6px; }
  .services__list { list-style: none; font-size: 16.5px; line-height: 1.35; }
  .services__list li { display: flex; align-items: center; gap: 9px; }
  .services__list li::before { content: ""; width: 9px; height: 9px; background: var(--white); flex: none; }
</style>
</head>
<body>
<main class="sheet">

  <section class="card card--front" aria-label="Business card front">
    <svg class="card__band" viewBox="0 0 620 354" aria-hidden="true">
      <polygon points="0,272 230,272 252,292 620,292 620,354 0,354" fill="var(--band-line)"/>
      <polygon points="0,280 226,280 248,300 620,300 620,354 0,354" fill="var(--band-grey)"/>
      <polygon points="0,290 222,290 244,310 620,310 620,314 244,314 222,294 0,294" fill="var(--band-line)" opacity=".8"/>
    </svg>
    <h1 class="owner">Rodrigo Fenwar</h1>
    <ul class="contact">
      <li>
        <svg viewBox="0 0 24 24"><path d="M6.6 10.8a15.5 15.5 0 0 0 6.6 6.6l2.2-2.2a1 1 0 0 1 1-.25 11.4 11.4 0 0 0 3.6.57 1 1 0 0 1 1 1V20a1 1 0 0 1-1 1A17 17 0 0 1 3 4a1 1 0 0 1 1-1h3.5a1 1 0 0 1 1 1c0 1.25.2 2.45.57 3.57a1 1 0 0 1-.25 1z" fill="var(--brand-blue)"/></svg>
        801-437-2190
      </li>
      <li>
        <svg viewBox="0 0 24 24"><rect x="2" y="5" width="20" height="14" fill="var(--brand-blue)"/><path d="M2 5l10 8 10-8" fill="none" stroke="var(--white)" stroke-width="1.6"/></svg>
        Fenwarcoatings.utah@brelmox.com
      </li>
    </ul>
    <div class="brand brand--front">
      <span class="brand__mark" aria-hidden="true"></span>
      <span>
        <span class="brand__name">Fenwar</span>
        <span class="brand__sub">Coatings</span>
      </span>
    </div>
  </section>

  <section class="card card--back" aria-label="Business card back">
    <svg class="card__band" viewBox="0 0 620 354" aria-hidden="true">
      <polygon points="0,262 250,262 272,290 620,290 620,354 0,354" fill="var(--band-line)"/>
      <polygon points="0,270 246,270 268,298 620,298 620,354 0,354" fill="var(--band-grey)"/>
    </svg>
    <div class="brand brand--back">
      <span class="brand__mark" aria-hidden="true"></span>
      <span>
        <span class="brand__name">Fenwar</span>
        <span class="brand__sub">Coatings</span>
      </span>
    </div>
    <div class="services">
      <h2 class="services__title">SERVICES</h2>
      <ul class="services__list">
        <li>Custom Paint &amp; Stain</li>
        <li>Interior &amp; Exterior</li>
        <li>Epoxy Coatings / Garage Floors</li>
        <li>Cabinet Refinishing</li>
        <li>Log Staining and Refinishing.</li>
      </ul>
    </div>
  </section>

</main>
</body>
</html>
```